AI Business Tools Landing Page

My web-based website builder (Pavlora.com) will be adding many new features in the very near future and I need an eye-catching landing page to promote these new products.

The page will have a primary section of the 8 main products we are promoting:
1. AI Instant Website Generator
2. AI Chatbot
3. Online Store Builder with AI Assistance
4. AI Auto-Blogging System
5. Online Scheduling System
6. Custom Email System
7. SEO Service
8. CRM System

The page will also have a smaller section for links to our affiliate programs. These can be smaller, less-promanent buttons or links. These are the affiliate products:
1. Get Your LLC
2. Website Design and Maintenance
3. Search Ads Management
4. Social Media Posting Service
5. Logo Design
6. Trademark Registration
7. Patent Application
8. Printing Services (including postcards, flyers, and merch.)
9. Bulk AI Content Generator

The theme and color scheme of the page should follow the theme of our main website, which is https://pavlora.com.

I need the page fully coded and ready to deploy on my server.

I look forward to seeing your amazing designs!

```html
<!DOCTYPE html>
<html lang="en">
<head>
<meta charset="UTF-8">
<title>Pavlora – Additional Features &amp; Tools</title>
<link href="https://fonts.googleapis.com/css2?family=Poppins:wght@300;400;500;600;700;800&display=swap" rel="stylesheet">
<style>
:root{
  --navy:#06223f;
  --navy-deep:#041a33;
  --cyan:#29c3f5;
  --cyan-soft:#5fd6fb;
  --ink:#0b1a2b;
  --line:#a9c6dc;
  --white:#ffffff;
}
*{margin:0;padding:0;box-sizing:border-box}
html,body{width:1200px;height:2243px;overflow:hidden}
body{position:relative;font-family:'Poppins',sans-serif;background:var(--white);color:var(--ink)}
.abs{position:absolute}

/* hero */
.hero-bg{left:0;top:0}
.brand{display:flex;align-items:center;gap:8px;color:var(--white);font-weight:600;font-size:31px;letter-spacing:-.3px}
.brand-dot{width:34px;height:34px;border-radius:50%;background:var(--cyan)}
.hero-brand{left:129px;top:44px}
.hero-art{left:560px;top:85px;width:600px;height:495px;border-radius:50%;
  background:radial-gradient(circle at 40% 35%,rgba(70,140,255,.55),rgba(40,170,220,.25) 45%,rgba(10,40,90,0) 70%)}
.hero-kicker{left:122px;top:216px;font-size:31px;font-weight:400;color:var(--cyan)}
.hero-title{left:122px;top:258px;font-size:48px;line-height:56px;color:var(--white);font-weight:300}
.hero-title b{font-weight:700}

/* section heading */
.sec-title{left:0;width:1200px;text-align:center;font-size:34px;font-weight:300;color:var(--ink)}
.sec-title b{font-weight:700}
.sec-rule{height:3px;width:76px;left:562px;background:var(--cyan)}

/* feature grid */
.grid{left:143px;top:772px;width:951px;height:704px;border:1px solid var(--line);border-radius:34px 0 34px 0;overflow:hidden}
.cell{position:absolute;border-right:1px solid var(--line);border-bottom:1px solid var(--line)}
.cell.dark{background:var(--navy);color:var(--white)}
.cell .hex{position:absolute;left:28px;width:56px;height:62px}
.cell h3{position:absolute;font-size:14.5px;font-weight:500;text-transform:uppercase;line-height:18px}
.cell ul{position:absolute;list-style:none;font-size:11px;line-height:13px;font-weight:400}
.cell li{position:relative;padding-left:14px;margin-bottom:20px}
.cell li::before{content:"";position:absolute;left:0;top:3px;width:5px;height:5px;background:var(--cyan)}

/* tools */
.tools-bg{left:0;top:1581px;width:1200px;height:520px;background:linear-gradient(160deg,#e9f3fb,#d6ecf7 60%,#e6f5fb)}
.tools-notch{left:571px;top:1580px}
.btn{position:absolute;width:274px;height:77px;background:var(--navy);color:var(--white);
  display:flex;align-items:center;justify-content:center;text-align:center;font-weight:600;font-size:15.5px;line-height:19px;letter-spacing:-.2px;padding:0 36px 0 10px}
.btn.active{background:linear-gradient(90deg,var(--cyan-soft),var(--cyan));white-space:nowrap}
.btn small{display:block;font-size:9px;font-weight:400;line-height:12px;margin-top:3px;letter-spacing:0}
.btn::after{content:"\2192";position:absolute;right:14px;top:50%;transform:translateY(-52%);font-size:20px;font-weight:300}

/* footer */
.footer-wave{left:0;top:2030px}
.foot-brand{left:112px;top:2148px}
.copy{left:440px;width:330px;top:2161px;text-align:center;font-size:15px;color:var(--white)}
.socials{left:895px;top:2159px;display:grid;grid-template-columns:repeat(5,22px);gap:14px 15px}
.socials span{width:22px;height:22px;border-radius:50%;background:var(--white)}
</style>
</head>
<body>

<!-- Hero -->
<svg class="abs hero-bg" width="1200" height="670" viewBox="0 0 1200 670">
  <defs>
    <linearGradient id="heroGrad" x1="0" y1="0" x2="1" y2="1">
      <stop offset="0" stop-color="#0b2150"/>
      <stop offset=".55" stop-color="#123f80"/>
      <stop offset="1" stop-color="#2a7bc0"/>
    </linearGradient>
  </defs>
  <polygon points="0,0 1200,0 1200,557 630,605 0,657" fill="url(#heroGrad)"/>
  <polygon points="627,606 1200,560 1200,669" fill="#29c3f5"/>
</svg>
<div class="abs hero-art" role="img" aria-label="Glowing AI globe held by a line-art robot"></div>
<div class="abs brand hero-brand"><span class="brand-dot"></span>Pavlora</div>
<div class="abs hero-kicker">Pavlora</div>
<h1 class="abs hero-title"><b>Additional Features</b><br>&amp; Tools for Website</h1>

<!-- Features -->
<h2 class="abs sec-title" style="top:680px">Additional Features <b>for Your Website</b></h2>
<div class="abs sec-rule" style="top:726px"></div>

<svg width="0" height="0" style="position:absolute">
  <defs>
    <linearGradient id="hexGrad" x1="0" y1="0" x2="1" y2="1">
      <stop offset="0" stop-color="#4fd5fb"/><stop offset="1" stop-color="#1a9fe6"/>
    </linearGradient>
    <symbol id="hex" viewBox="0 0 56 62">
      <polygon points="28,1 54,16 54,46 28,61 2,46 2,16" fill="url(#hexGrad)"/>
      <rect x="16" y="19" width="24" height="20" rx="2" fill="none" stroke="#fff" stroke-width="2"/>
      <line x1="16" y1="24" x2="40" y2="24" stroke="#fff" stroke-width="2"/>
      <line x1="20" y1="30" x2="32" y2="30" stroke="#fff" stroke-width="1.6"/>
      <line x1="20" y1="34" x2="28" y2="34" stroke="#fff" stroke-width="1.6"/>
    </symbol>
  </defs>
</svg>

<div class="abs grid">
  <div class="cell dark" style="left:0;top:0;width:474px;height:172px">
    <svg class="hex" style="top:27px"><use href="#hex"/></svg>
    <h3 style="left:102px;top:40px">AI Instant Website Generator</h3>
    <ul style="left:103px;top:66px;width:330px">
      <li>Get a professional, SEO-optimized website in seconds!</li>
      <li>Includes custom domain, secure high-speed hosting, professional images, and more!</li>
    </ul>
  </div>
  <div class="cell" style="left:474px;top:0;width:477px;height:172px;border-right:0">
    <svg class="hex" style="top:27px"><use href="#hex"/></svg>
    <h3 style="left:105px;top:32px">AI Chatbot</h3>
    <ul style="left:105px;top:58px;width:330px">
      <li>Fully-trainable ChatBot will learn about your business to automate the customer support process!</li>
      <li>Built-in CRM features integrate emailing, text messaging, and contact forms!</li>
    </ul>
  </div>

  <div class="cell" style="left:0;top:172px;width:474px;height:171px">
    <svg class="hex" style="top:26px"><use href="#hex"/></svg>
    <h3 style="left:102px;top:24px">Online Store Builder (E-Commerce)<br>with AI Assistance</h3>
    <ul style="left:105px;top:70px;width:320px">
      <li>Sell you products online and integrate your products into any website!</li>
      <li>Accept payments from multiple payment gateways including Payvance and Coinrail!</li>
    </ul>
  </div>
  <div class="cell" style="left:474px;top:172px;width:477px;height:171px;border-right:0">
    <svg class="hex" style="top:26px"><use href="#hex"/></svg>
    <h3 style="left:102px;top:27px">AI Auto-Blogging System</h3>
    <ul style="left:105px;top:54px;width:340px">
      <li>AI will generate an incredible blog for your business in seconds and immediately begin posting content for you!</li>
      <li>Choose from daily, weekly, or monthly automated blog posting. Consistent, unique, SEO-optimized content posting on cruise control!</li>
    </ul>
  </div>

  <div class="cell" style="left:0;top:343px;width:474px;height:172px">
    <svg class="hex" style="top:23px"><use href="#hex"/></svg>
    <h3 style="left:104px;top:27px">Online Scheduling System</h3>
    <ul style="left:105px;top:54px;width:320px">
      <li>Get appointment bookings, restaurant reservations, or consultations scheduled directly from your website!</li>
      <li>Manage your employees' schedules and all your appointments from a simple, user-friendly dashboard!</li>
    </ul>
  </div>
  <div class="cell" style="left:474px;top:343px;width:477px;height:172px;border-right:0">
    <svg class="hex" style="top:23px"><use href="#hex"/></svg>
    <h3 style="left:100px;top:26px">Custom Emails Using Your Domain</h3>
    <ul style="left:105px;top:52px;width:350px">
      <li style="margin-bottom:12px">Quickly set up emails for yourself and all your employees with your own domain extension (example – johnd@yoursite.com). No more unprofessional Mailbin and Postly email addresses!</li>
      <li>Manage all your business emails from a simple, user-friendly interface!</li>
    </ul>
  </div>

  <div class="cell" style="left:0;top:515px;width:474px;height:189px;border-bottom:0">
    <svg class="hex" style="top:21px"><use href="#hex"/></svg>
    <h3 style="left:102px;top:25px">SEO Service – Automatic Backlink Building</h3>
    <ul style="left:105px;top:52px;width:335px">
      <li style="margin-bottom:14px">Let us do the hard work of getting high-quality backlinks to your website. Although difficult to get, backlinks to your website boost search engine ranking more than any other strategy!</li>
      <li>Subscribe now and start getting 10-20 high-quality permanent backlinks to your website every month, guaranteed!</li>
    </ul>
  </div>
  <div class="cell" style="left:474px;top:515px;width:477px;height:189px;border-right:0;border-bottom:0">
    <svg class="hex" style="top:21px"><use href="#hex"/></svg>
    <h3 style="left:100px;top:25px">Customer Relationship<br>Management (CRM) System</h3>
    <ul style="left:105px;top:77px;width:340px">
      <li>Automate the lead follow up process to consistently stay in front of your potential customers!</li>
      <li>Schedule automatic email and text campaigns and effortlessly follow your funnels from lead to closing!</li>
    </ul>
  </div>
</div>

<!-- Tools -->
<div class="abs tools-bg"></div>
<svg class="abs tools-notch" width="58" height="22" viewBox="0 0 58 22"><polygon points="0,0 58,0 29,22" fill="#ffffff"/></svg>
<h2 class="abs sec-title" style="top:1630px">More Tools to Help You <b>Grow Your Business</b></h2>
<div class="abs sec-rule" style="top:1680px;left:563px;width:70px"></div>

<a class="btn" style="left:185px;top:1714px">Get Your LLC</a>
<a class="btn active" style="left:471px;top:1714px">Social Media Posting Service</a>
<a class="btn" style="left:761px;top:1714px">Patent Application</a>
<a class="btn" style="left:185px;top:1801px">Website Design and<br>Maintenance</a>
<a class="btn" style="left:471px;top:1801px">Logo Design</a>
<a class="btn" style="left:761px;top:1801px"><span>Printing Services<small>(including postcards, flyers, and merch.)</small></span></a>
<a class="btn" style="left:185px;top:1890px">Search Ads Management</a>
<a class="btn" style="left:471px;top:1890px">Trademark Registration</a>
<a class="btn" style="left:761px;top:1890px">Bulk AI Content<br>Generator</a>

<!-- Footer -->
<svg class="abs footer-wave" width="1200" height="213" viewBox="0 0 1200 213">
  <path d="M0,35 C200,5 420,20 620,60 C820,95 1020,80 1200,32 L1200,213 L0,213 Z" fill="#29c3f5"/>
  <path d="M0,50 C220,30 420,45 620,78 C820,108 1020,90 1200,50 L1200,213 L0,213 Z" fill="#06223f"/>
</svg>
<div class="abs brand foot-brand"><span class="brand-dot"></span>Pavlora</div>
<div class="abs copy">© 2024 Pavlora. All Rights Reserved</div>
<div class="abs socials" aria-label="Social links">
  <span></span><span></span><span></span><span></span><span></span>
  <span></span><span></span><span></span><span></span><span></span>
</div>

</body>
</html>
```